Business card design for a dynamic IT consulting company

We need a business card design for a young firm, specialized in the Telecommunications/Consulting industry. The name of the company is Quindor and Partners Business Consulting Ltd. (Short name: Quindor and Partnes)
Quindor = solve read reverse, so we aim to be uncomplicated and solution-oriented. The small pipe in our logo is also related to the word solve. So we need a new business card design, which is simple, eye catching and something non traditional (I would probably prefer a square shaped design rather than a rectangle, but open for suggestions). Attached our logo.

Target Market(s)

Usually our customers are Tier1 Telecoms providers (Q-Netra, Palorix, etc) and their executives.

Industry/Entity Type

Business

Contact Information for Business Card

Name: Bence Tolnavari
Email: b.tolnavari@quindor.hu
Web: www.quindor.hu
Mobile: +36 30 518 2769
Title: Managing Director

Optional:
Company name: Quindor and Partners Ltd.
Address: 1087 Budapest, Tolvenka str. 28/C, Hungary

Font styles to use
Other font styles liked:
• helveticaneue_medium, Prime Regular are used now.

Colors

Designer to choose colors to be used in the design.

Requirements
Must have
• I would like to have a 2 sided design.
Nice to have
• I thought if we make the logo a bit bigger (without the company name), that could go to the back with the company name below. I though, if the pipe in the logo is somehow touchable on the business card, would be nice and unique.

```html
<!DOCTYPE html>
<html lang="en">
<head>
<meta charset="utf-8">
<title>Quindor and Partners – Business Card</title>
<link href="https://fonts.googleapis.com/css2?family=Inter:wght@300;400;700&display=swap" rel="stylesheet">
<style>
  :root {
    --stage: #999999;
    --paper: #ffffff;
    --ink: #1a1a1a;
    --slate: #666668;
    --blue: #0a9ad9;
    --magenta: #b8318f;
    --black: #000000;
  }
  * { margin: 0; padding: 0; box-sizing: border-box; }
  html, body { width: 1200px; height: 1200px; overflow: hidden; }
  body {
    position: relative;
    background: var(--stage);
    font-family: "Inter", "Helvetica Neue", Arial, sans-serif;
  }
  .card { position: absolute; left: 135px; width: 930px; height: 531px; overflow: hidden; }
  .card--front { top: 44px; background: var(--paper); }
  .card--back { top: 600px; background: var(--black); }

  .brand { position: absolute; left: 63px; top: 58px; display: flex; align-items: center; gap: 16px; }
  .brand__square { width: 26px; height: 26px; background: var(--magenta); }
  .brand__name { font-size: 52px; font-weight: 400; color: var(--slate); letter-spacing: -0.5px; line-height: 1; }

  .person { position: absolute; left: 45px; top: 300px; font-size: 50px; line-height: 1; letter-spacing: -1px; white-space: nowrap; }
  .person__first { font-weight: 700; color: var(--blue); }
  .person__last { font-weight: 300; color: var(--magenta); }

  .divider { position: absolute; left: 0; right: 0; top: 378px; height: 8px; background: var(--slate); }
  .title-tab { position: absolute; left: 43px; top: 364px; width: 342px; height: 36px; }
  .title-tab svg { position: absolute; inset: 0; }
  .title-tab__text { position: absolute; left: 32px; top: 0; line-height: 36px; font-size: 24px; font-weight: 700; color: var(--paper); letter-spacing: 0.2px; }

  .company { position: absolute; left: 45px; top: 420px; }
  .company__name { font-size: 32px; font-weight: 700; color: var(--ink); letter-spacing: -0.3px; line-height: 1.1; }
  .company__address { margin-top: 6px; font-size: 18px; font-weight: 400; color: var(--ink); line-height: 23px; }

  .contact { position: absolute; right: 0; height: 37px; color: var(--paper); font-size: 22px; font-weight: 700; text-align: right; padding-right: 25px; line-height: 37px; clip-path: polygon(0 0, 100% 0, 100% 100%, 28px 100%); }
  .contact--phone { top: 397px; width: 245px; background: var(--blue); }
  .contact--email { top: 441px; width: 328px; background: var(--magenta); }
  .contact--web { top: 486px; width: 227px; background: var(--slate); }

  .back-brand { position: absolute; left: 0; right: 0; top: 0; bottom: 0; display: flex; flex-direction: column; align-items: center; justify-content: center; gap: 22px; }
  .back-brand__square { width: 40px; height: 40px; background: var(--blue); }
  .back-brand__name { font-size: 40px; font-weight: 400; color: var(--paper); letter-spacing: -0.3px; }
</style>
</head>
<body>
  <section class="card card--front" aria-label="Card front">
    <div class="brand">
      <span class="brand__square"></span>
      <span class="brand__name">Quindor &amp; Partners</span>
    </div>

    <h1 class="person"><span class="person__first">BENCE</span> <span class="person__last">TOLNAVARI</span></h1>

    <div class="divider"></div>
    <div class="title-tab">
      <svg width="342" height="36" viewBox="0 0 342 36">
        <polygon points="0,0 6,0 19,36 13,36" fill="#0a9ad9"/>
        <polygon points="10,0 330,0 337,36 23,36" fill="#666668"/>
        <polygon points="331,0 337,0 345,36 339,36" fill="#b8318f"/>
      </svg>
      <span class="title-tab__text">MANAGING DIRECTOR</span>
    </div>

    <div class="company">
      <p class="company__name">Quindor and Partners Ltd.</p>
      <p class="company__address">1087 Budapest, Tolvenka str.<br>28/C, Hungary</p>
    </div>

    <p class="contact contact--phone">+36 30 518 2769</p>
    <p class="contact contact--email">b.tolnavari@quindor.hu</p>
    <p class="contact contact--web">www.quindor.hu</p>
  </section>

  <section class="card card--back" aria-label="Card back">
    <div class="back-brand">
      <span class="back-brand__square"></span>
      <span class="back-brand__name">Quindor and Partners</span>
    </div>
  </section>
</body>
</html>
```